New and upgraded www.valdmorefunds.com content & design financial markets

We need an upgrade of our site. The current site is www.valdmorefunds.com
Navigation with full site map i.e. the user can select any page from any menu item.

The “Insights” (Insikter) page will remain as is except new design AND with far more possibilities to add thumbnails, picts, videos etc. The user will have to logon to be able to read the full story.

The “Produkter & Tjänster” (“How to invest” in current web) will contain about the same info as the current “How to invest” pages.

Some pages will contain one or more videos and or speaker supported “live” graphics which we will supply. The media content shall be easy to change.

The site will have two languages from start, English and Swedish. There will be more languages added within 1 year or slightly more.

All texts will be provided by us.

I’m attaching a PDF with suggested content for some of the new pages. However this is just content and absolutely no design. We need new design for the total of the site as well as for the graphics.

Expectation info:
These sites (Both major players in our business) can be used as inspiration:
https://www.tarvenholm.com/eu/en/
https://www.brightwellpartners.com/index.html

Below some opt-OUT and opt-IN graphic rules in connection with the Web supporting our business acumen and brand:

Opt-OUT:
- images similar to educational comic books - it signals an authoritarian approach where the customer is small (insubstantial).
- images that signal trading, cyber, mystery and fast-paced business. We are extremely long-term and invest in real companies
- avoid images containing coins, calculators and banknotes. We're not a savings bank company. or payment service-branch
- avoid images of large data flows, because we should not make facts complex, but simple and comprehensible
- avoid sensing pictures of photo models. We are real people who stand for our efforts. We're not going to hide.
- avoid pictures of suits and tie. They signal rigid-banking. We're smart-investment, flexible, adaptable. Rather curl up your sleeves and show that we’re building something valuable.
- avoid pictures of skyscrapers and cool bank pictures - because they signal the more old valuations of big capital and giant banks - that we are not at all. I know we've had clean facades before. As long as we're not talking about bank skyscrapers, I'm in.

Opt-IN
- pictures of Lukas in moderate amount - he is our symbol person
- films with Lukas and explaining graphical films - explaining and clarifying
- images of pedagogy that give the customer a sense of overview and insights that we give to the customers in our service
- illustrations that explain and deepen our work
- pictures and bars that in 3d illustrate our consistent results and stable delivery
- images that signal that we have a full grasp of data, flows and analyses - without the image becoming a space adventure
- use the logo as a grid, shape and colour.
- no genre portraits, rather pictures of real customers - which gives a sense of why they are customers here
- images that support our core i.e. is science, innovation, unrestricted thinking (“out of the box” – (don’t like that sentence)), smart-solutions, data-driven, client-cantered, flexible and adaptable to client needs and expectation.
- Solid - to be trustworthy in any economic climate
- Long term - consistent work and choices. No trading. Numbers talk
- Data-driven - real tech - combining years of work in finance with straight on tech

Presenting on the webpage:
The story in text and illustration
Show the truth - we have a great history to show and give space
Only numbers and graphs that has a meaning - no artificial numbers etc.
Updates

Target Market(s)

Europe

Coding

Coded - Design and coding required

Number of Pages Required

5+ page

Colors

Designer to choose colors to be used in the design.

Requirements
Must have
• Colours in line with www.valdmorefunds.com

```html
<!DOCTYPE html>
<html lang="en">
<head>
<meta charset="utf-8">
<title>Valdmore Funds — Your Personal Investment Advisor</title>
<link href="https://fonts.googleapis.com/css2?family=Rajdhani:wght@600;700&family=Roboto:wght@300;400;500&display=swap" rel="stylesheet">
<style>
:root{
  --blue:#0d55c9;
  --blue-bright:#1660d6;
  --navy:#06186b;
  --ink:#111;
  --text:#333;
  --muted:#8a8a8a;
  --grey-bg:#f3f3f3;
  --white:#fff;
}
*{margin:0;padding:0;box-sizing:border-box}
html,body{width:1200px;height:4365px;overflow:hidden;background:var(--white)}
body{font-family:'Roboto',Arial,sans-serif;color:var(--text);position:relative}
.abs{position:absolute}
.heading{font-family:'Rajdhani','Roboto',sans-serif;font-weight:700;color:var(--ink)}
.btn{position:absolute;display:flex;align-items:center;justify-content:center;font-size:14px;color:var(--white);background:var(--blue);outline:2px solid var(--blue);outline-offset:3px;letter-spacing:.3px}
.btn.on-navy{outline-color:var(--blue-bright)}
.photo{position:absolute}
/* header */
.header-panel{left:388px;top:0;width:812px;height:739px;background:var(--blue)}
.logo{display:flex;align-items:center;gap:12px;font-family:'Roboto',sans-serif;font-weight:300;font-size:32px;color:var(--navy)}
.logo .mark{width:22px;height:22px;background:var(--navy)}
.nav{left:449px;top:30px;display:flex;gap:26px;font-size:14px;color:rgba(255,255,255,.78);letter-spacing:.2px}
.nav .active{color:var(--white);font-weight:500}
.hero-photo{left:76px;top:83px;width:1046px;height:573px;background:linear-gradient(135deg,#2c3340 0%,#161c29 45%,#0c1430 75%,#1a2a5a 100%)}
.hero-title{left:76px;width:1046px;top:278px;text-align:center;font-family:'Rajdhani',sans-serif;font-weight:700;font-size:62px;line-height:66px;color:var(--white)}
.hero-sub{left:76px;width:1046px;top:430px;text-align:center;font-size:21px;color:var(--white);font-weight:300}
/* about */
.eyebrow{font-family:'Rajdhani',sans-serif;font-weight:700;font-size:20px;color:var(--blue)}
.h2{font-size:40px;line-height:44px}
.body-small{font-size:13.5px;line-height:27px;color:var(--muted)}
/* focus */
.navy-box{background:var(--navy);color:var(--white)}
.focus-text{left:76px;width:500px;text-align:center}
/* approach */
.feature{position:absolute;width:230px;text-align:center}
.feature h3{font-size:15.5px;font-weight:500;line-height:26px;color:var(--ink);margin-top:18px}
.feature p{font-size:13px;line-height:26px;color:var(--muted);margin-top:10px}
/* why */
.card-label{font-family:'Rajdhani',sans-serif;font-weight:600;font-size:25px;line-height:40px;color:#222}
/* footer */
.footer{left:0;top:3898px;width:1200px;height:467px;background:var(--grey-bg)}
.f-head{font-family:'Rajdhani',sans-serif;font-weight:700;font-size:23px;color:var(--ink)}
.f-links{font-size:13px;line-height:25px;color:#555;list-style:none}
.contact{font-size:13px;line-height:26px;color:#555}
.contact b{color:var(--blue);font-weight:400;font-size:15.5px}
.social{width:46px;height:46px;background:var(--blue)}
</style>
</head>
<body>

<!-- Header -->
<div class="abs header-panel"></div>
<div class="abs logo" style="left:78px;top:22px"><span class="mark"></span>Valdmore Funds</div>
<nav class="abs nav">
  <span class="active">HOME</span><span>PHILOSOPHY</span><span>HOW TO INVEST</span><span>WHAT WE DO</span><span>CONTACT</span><span>INSIGHTS</span>
</nav>
<svg class="abs" style="left:1101px;top:31px" width="22" height="22" viewBox="0 0 22 22" fill="none" stroke="#fff" stroke-width="2"><circle cx="9" cy="9" r="7"/><path d="M14 14l6 6"/></svg>

<!-- Hero -->
<div class="photo hero-photo" role="img" aria-label="Advisor and client shaking hands over a desk with charts and a laptop"></div>
<svg class="abs" style="left:76px;top:83px" width="1046" height="573" viewBox="0 0 1046 573" fill="none" stroke="#1a55c4" stroke-width="8">
  <path d="M165 377V163h560"/>
  <path d="M889 155v340H612"/>
</svg>
<h1 class="abs hero-title">YOUR PERSONAL<br>INVESTMENT ADVISOR</h1>
<p class="abs hero-sub">Valdmore Funds is Your Global Reference for Investment Advice</p>
<svg class="abs" style="left:128px;top:686px" width="200" height="24" viewBox="0 0 200 24" fill="none">
  <path d="M2 12h28M2 12l6-5M2 12l6 5" stroke="#06186b" stroke-width="2"/>
  <circle cx="70" cy="12" r="8" stroke="#06186b" stroke-width="1.5"/><circle cx="70" cy="12" r="4" fill="#06186b"/>
  <circle cx="101" cy="12" r="6" stroke="#bbb" stroke-width="1.5"/><circle cx="101" cy="12" r="2.5" fill="#bbb"/>
  <circle cx="131" cy="12" r="6" stroke="#bbb" stroke-width="1.5"/><circle cx="131" cy="12" r="2.5" fill="#bbb"/>
  <path d="M168 12h28M196 12l-6-5M196 12l-6 5" stroke="#06186b" stroke-width="2"/>
</svg>

<!-- About -->
<p class="abs eyebrow" style="left:80px;top:802px">Welcome To Valdmore Funds</p>
<h2 class="abs heading h2" style="left:80px;top:834px">About Company</h2>
<p class="abs body-small" style="left:500px;top:829px;width:620px">We are a privately held firm dedicated to clients who have entrusted us with their wealth. We act solely and transparently in the best interest of our clients. We pride ourselves on our discretion and confidentiality.</p>
<p class="abs body-small" style="left:500px;top:933px;width:620px">You can be assured of a totally Client-centric service, high quality, totally unbiased, investment advice. We are fee only based, i.e. we have no affiliations with any financial institutions - we do not take any commission from any investment product provider - We Work Only for You!</p>
<div class="btn" style="left:503px;top:1045px;width:138px;height:50px">LEARN MORE</div>

<!-- Client Focus -->
<div class="photo" style="left:498px;top:1156px;width:624px;height:417px;background:linear-gradient(120deg,#b9b3a8 0%,#8d8a86 40%,#4b5564 75%,#2d3a52 100%)" role="img" aria-label="Advisor reviewing documents with an elderly couple on a sofa"></div>
<div class="abs navy-box" style="left:76px;top:1198px;width:500px;height:438px"></div>
<h2 class="abs heading focus-text" style="top:1249px;font-size:40px;color:#fff">Client Focus</h2>
<p class="abs focus-text" style="top:1314px;font-size:20px;line-height:32px;color:#fff">For Years Financial Institutions Have Said:<br>"Client in the Center"...</p>
<p class="abs focus-text" style="top:1387px;left:104px;width:444px;font-size:13px;line-height:27px;color:rgba(255,255,255,.8)">but they have mainly offered standard solutions without much flexibility leaving the client with a feeling that he is just a number in another box. For us, a client is a real human being who has intentions and ambitions for his portfolio.</p>
<div class="btn on-navy" style="left:259px;top:1528px;width:135px;height:45px">LEARN MORE</div>

<!-- Our Approach -->
<div class="abs" style="left:0;top:1698px;width:781px;height:322px;background:var(--grey-bg)"></div>
<h2 class="abs heading h2" style="left:80px;top:1761px">Our Approach</h2>
<p class="abs" style="left:80px;top:1830px;width:620px;font-size:20px;line-height:32px;color:#444">Valdmore Funds is truly different - We deliver Investment Services that sets us apart from our contemporaries.</p>

<svg class="abs" style="left:401px;top:1941px" width="130" height="148" viewBox="0 0 130 148">
  <polygon points="65,3 126,38 126,110 65,145 4,110 4,38" fill="#fff" stroke="#0d55c9" stroke-width="2"/>
  <polygon points="65,12 118,43 118,105 65,136 12,105 12,43" fill="#1c3b86"/>
  <g fill="none" stroke="#fff" stroke-width="2.5"><circle cx="50" cy="60" r="9"/><circle cx="68" cy="78" r="10"/><path d="M85 95V80M93 95V72M101 95V64"/><path d="M36 95h28"/></g>
</svg>
<svg class="abs" style="left:669px;top:1941px" width="130" height="148" viewBox="0 0 130 148">
  <polygon points="65,3 126,38 126,110 65,145 4,110 4,38" fill="#fff" stroke="#0d55c9" stroke-width="2"/>
  <polygon points="65,12 118,43 118,105 65,136 12,105 12,43" fill="#1259c7"/>
  <g fill="none" stroke="#fff" stroke-width="2.5"><rect x="34" y="46" width="62" height="42" rx="2"/><path d="M55 100h20M65 88v12"/><circle cx="65" cy="67" r="12"/><path d="M65 67V55M65 67h12"/></g>
</svg>
<svg class="abs" style="left:938px;top:1941px" width="130" height="148" viewBox="0 0 130 148">
  <polygon points="65,3 126,38 126,110 65,145 4,110 4,38" fill="#fff" stroke="#0d55c9" stroke-width="2"/>
  <polygon points="65,12 118,43 118,105 65,136 12,105 12,43" fill="#06186b"/>
  <g fill="none" stroke="#fff" stroke-width="2.5"><circle cx="48" cy="62" r="8"/><path d="M34 98c0-14 6-22 14-22s14 8 14 22"/><circle cx="80" cy="58" r="9"/><circle cx="80" cy="58" r="3"/><path d="M62 80l10-8"/></g>
</svg>

<div class="feature" style="left:351px;top:2118px"><h3>Valdmore Investment<br>Management System VIMS®</h3><p>Built on a combination of macroeconomic and fundamental analysis</p></div>
<div class="feature" style="left:619px;top:2118px"><h3>VIQS ® Investment<br>Generator</h3><p>Valdmore iQ Software VIQS® is designed to analyse, forcast, generate and monitor an infinite...</p></div>
<div class="feature" style="left:888px;top:2118px"><h3>Services</h3><p style="margin-top:8px">VIMS® &amp; VIQS® enable Valdmore Funds to deliver customized services &amp; solutions to low cost &amp; risks with predictable...</p></div>

<!-- Why Choose Us -->
<h2 class="abs heading h2" style="left:80px;top:2334px">Why Choose Us</h2>
<div class="abs" style="left:98px;top:2712px;width:504px;height:112px;background:var(--blue)"></div>
<div class="photo" style="left:76px;top:2427px;width:500px;height:261px;background:linear-gradient(130deg,#6b4a35 0%,#a58a70 40%,#d9d2c8 70%,#8a8f96 100%)" role="img" aria-label="Team of colleagues working together at a laptop"></div>
<div class="abs" style="left:76px;top:2688px;width:43px;height:72px;background:#111"></div>
<div class="abs" style="left:119px;top:2688px;width:457px;height:118px;background:#fff"></div>
<p class="abs card-label" style="left:152px;top:2704px">Valdmore Investment Advisory<br>Philosophy</p>
<svg class="abs" style="left:543px;top:2741px" width="32" height="14" viewBox="0 0 32 14" fill="none" stroke="#0d55c9" stroke-width="2"><path d="M0 7h30M30 7l-6-5M30 7l-6 5"/></svg>

<div class="photo" style="left:602px;top:2500px;width:498px;height:261px;background:linear-gradient(120deg,#e6e9ec 0%,#b9c0c8 35%,#3b3f48 65%,#c9d0d8 100%)" role="img" aria-label="Two advisors discussing figures on a tablet"></div>
<div class="photo" style="left:602px;top:2712px;width:38px;height:122px;background:linear-gradient(180deg,#cfd4da,#8b939c)" role="img" aria-label="Edge of office photograph"></div>
<p class="abs card-label" style="left:675px;top:2787px">Valdmore Funds Investment<br>Strategy</p>
<svg class="abs" style="left:1060px;top:2822px" width="32" height="14" viewBox="0 0 32 14" fill="none" stroke="#06186b" stroke-width="2"><path d="M0 7h30M30 7l-6-5M30 7l-6 5"/></svg>

<!-- Thinking Beyond -->
<h2 class="abs heading h2" style="left:0;width:1200px;text-align:center;top:2958px">Thinking Beyond</h2>
<p class="abs" style="left:300px;width:600px;top:3030px;text-align:center;font-size:20px;line-height:32px;color:#444">Everything around us is changing in an accelerating pace, so shouldn't the financial markets change too?</p>
<p class="abs body-small" style="left:300px;width:600px;top:3100px;text-align:center">We asked ourselves - is this really how wealth management and investing should work? Is it really necessary to treat clients as just a number in a box? Is this how services should be delivered? How about flexibility?</p>
<div class="btn" style="left:530px;top:3215px;width:138px;height:47px">LEARN MORE</div>

<!-- Investment Intelligence -->
<div class="abs navy-box" style="left:498px;top:3334px;width:624px;height:458px"></div>
<div class="photo" style="left:76px;top:3397px;width:500px;height:437px;background:linear-gradient(150deg,#3d4452 0%,#8e9099 35%,#d8d6d2 65%,#b8bfc9 100%)" role="img" aria-label="Woman analysing printed charts next to a laptop"></div>
<h2 class="abs heading" style="left:656px;top:3395px;font-size:40px;color:#fff">Investment Intelligence</h2>
<p class="abs" style="left:656px;top:3464px;width:440px;font-size:13.5px;line-height:27px;color:#fff">Your Exclusive Access to European and American Markets and to Our Innovative Investment Approach.</p>
<p class="abs" style="left:656px;top:3527px;width:462px;font-size:13px;line-height:27px;color:rgba(255,255,255,.8)">We attempt to design attractive long-term return portfolios, with low portfolio turnover, to better withstand fluctuating markets. Our investment process, VIMS, is built to re-allocate to low risk investments during long-term market declines and to follow or outperform.</p>
<div class="btn on-navy" style="left:659px;top:3673px;width:135px;height:46px">LEARN MORE</div>

<!-- Footer -->
<div class="abs footer"></div>
<h3 class="abs f-head" style="left:80px;top:3960px">Quick Links</h3>
<ul class="abs f-links" style="left:80px;top:4018px">
  <li>Home</li><li>Philosophy</li><li>How to invest</li><li>What we do</li><li>Insight</li><li>Contact</li>
</ul>

<h3 class="abs f-head" style="left:347px;top:3960px">Get In Touch</h3>
<svg class="abs" style="left:345px;top:4021px" width="16" height="20" viewBox="0 0 16 20" fill="#0d55c9"><path d="M8 0a8 8 0 0 0-8 8c0 6 8 12 8 12s8-6 8-12a8 8 0 0 0-8-8zm0 11a3 3 0 1 1 0-6 3 3 0 0 1 0 6z"/></svg>
<p class="abs contact" style="left:379px;top:4017px"><b>Valdmore Funds</b><br>14 Rue des Tilleuls<br>L-2210 Luxembourg</p>
<svg class="abs" style="left:345px;top:4117px" width="18" height="18" viewBox="0 0 24 24" fill="#0d55c9"><path d="M6.6 10.8a15.1 15.1 0 0 0 6.6 6.6l2.2-2.2a1 1 0 0 1 1-.25 11.4 11.4 0 0 0 3.6.57 1 1 0 0 1 1 1V20a1 1 0 0 1-1 1A17 17 0 0 1 3 4a1 1 0 0 1 1-1h3.5a1 1 0 0 1 1 1c0 1.25.2 2.45.57 3.6a1 1 0 0 1-.25 1z"/></svg>
<p class="abs contact" style="left:379px;top:4112px"><b>Telephone</b><br>+352 2140 5587</p>

<svg class="abs" style="left:614px;top:4021px" width="16" height="20" viewBox="0 0 16 20" fill="#0d55c9"><path d="M8 0a8 8 0 0 0-8 8c0 6 8 12 8 12s8-6 8-12a8 8 0 0 0-8-8zm0 11a3 3 0 1 1 0-6 3 3 0 0 1 0 6z"/></svg>
<p class="abs contact" style="left:647px;top:4017px"><b>Valdmore Funds</b><br>52, Harbour Lane SLM<br>1420 Sliema, Malta</p>
<svg class="abs" style="left:614px;top:4117px" width="18" height="18" viewBox="0 0 24 24" fill="#0d55c9"><path d="M6.6 10.8a15.1 15.1 0 0 0 6.6 6.6l2.2-2.2a1 1 0 0 1 1-.25 11.4 11.4 0 0 0 3.6.57 1 1 0 0 1 1 1V20a1 1 0 0 1-1 1A17 17 0 0 1 3 4a1 1 0 0 1 1-1h3.5a1 1 0 0 1 1 1c0 1.25.2 2.45.57 3.6a1 1 0 0 1-.25 1z"/></svg>
<p class="abs contact" style="left:647px;top:4112px"><b>Telephone</b><br>+356 2713 9046</p>

<h3 class="abs f-head" style="left:885px;top:3960px">Stay In Touch</h3>
<p class="abs" style="left:885px;top:4018px;width:235px;font-size:13px;line-height:25px;color:#555">To receive email releases, simply provide us with your email below</p>
<div class="abs" style="left:883px;top:4092px;width:239px;height:51px;background:#fff;border:1px solid #ddd"></div>
<p class="abs" style="left:896px;top:4110px;font-size:12px;color:#999">Your Email</p>
<svg class="abs" style="left:1081px;top:4111px" width="32" height="14" viewBox="0 0 32 14" fill="none" stroke="#0d55c9" stroke-width="2"><path d="M0 7h30M30 7l-6-5M30 7l-6 5"/></svg>

<div class="abs" style="left:0;top:4245px;width:1200px;height:1px;background:#ddd"></div>
<div class="abs" style="left:470px;top:4222px;width:260px;height:46px;background:var(--grey-bg)"></div>
<div class="abs logo" style="left:490px;top:4226px"><span class="mark"></span>Valdmore Funds</div>

<p class="abs" style="left:80px;top:4298px;font-size:12px;color:#777">© 2019 Valdmore Funds | All rights Reserved</p>
<div class="abs social" style="left:968px;top:4283px;opacity:.75" role="img" aria-label="Social network link"></div>
<div class="abs social" style="left:1022px;top:4283px;background:#1a8fe0" role="img" aria-label="Social network link"></div>
<div class="abs social" style="left:1076px;top:4283px" role="img" aria-label="Social network link"></div>

</body>
</html>
```